New Business Card Design Project

We require a business card design for Vexalund, a newly established Indian company.
Our focus is on the development, manufacturing, and export of a diverse array of pharmaceutical products on a global scale. The card should convey a professional appearance, as our primary markets are in Africa, China, and Southeast Asian nations.
We envision a two-sided business card, with the reverse side dedicated to a logo set against a solid color or an elegantly designed pattern. The corners should be rounded. We would appreciate seeing both horizontal and vertical design options. We trust the designer to utilize their expertise in creating this design.

The content for the business card is included in the attached Word file.

Target Market(s)

Our primary markets are in Africa, China, and Southeast Asian, Latin America, Maldives, Sri Lanka

Industry/Entity Type

Pharmaceutical Manufacturing and Export

Contact Information for Business Card

Colors

Designer to choose colors to be used in the design.

Requirements
Must have
• The reverse side of the business card features solely the logo along with the tagline, "Care Across Borders."
Should not have
• The logo should not exceed two instances, encompassing both the front and back sides of the card.

```html
<!DOCTYPE html>
<html lang="en">
<head>
<meta charset="utf-8">
<title>Vexalund — Business Card</title>
<link rel="stylesheet" href="https://fonts.googleapis.com/css2?family=Poppins:wght@700&family=Arimo:wght@400&display=swap">
<style>
  :root {
    --backdrop: #3b3b3b;
    --card-white: #ffffff;
    --brand-blue: #29a8e0;
    --brand-coral: #f0604d;
    --text-white: #ffffff;
    --text-grey: #4a4a4a;
    --radius: 22px;
  }
  * { margin: 0; padding: 0; box-sizing: border-box; }
  html, body {
    width: 1200px; height: 689px; overflow: hidden;
    background: var(--backdrop);
  }
  .canvas {
    position: relative; width: 1200px; height: 689px;
    background: var(--backdrop);
  }
  .card {
    position: absolute; top: 190px;
    width: 540px; height: 309px;
    border-radius: var(--radius);
    overflow: hidden;
  }
  /* Reverse side */
  .card-back {
    left: 40px;
    background: var(--card-white);
    display: flex; flex-direction: column; align-items: center; justify-content: center;
  }
  .brand-lockup { display: flex; align-items: center; gap: 12px; }
  .brand-dot {
    width: 22px; height: 22px; border-radius: 50%;
    background: var(--brand-coral);
  }
  .brand-name-back {
    font-family: "Poppins", sans-serif; font-weight: 700;
    font-size: 50px; line-height: 1; letter-spacing: 0.5px;
    color: var(--brand-blue);
  }
  .tagline {
    margin-top: 26px;
    font-family: "Arimo", sans-serif; font-size: 15px;
    color: var(--text-grey);
  }
  /* Front side */
  .card-front {
    left: 620px;
    background: var(--brand-blue);
    color: var(--text-white);
    font-family: "Arimo", sans-serif;
  }
  .front-content { position: absolute; left: 40px; top: 52px; }
  .brand-name-front {
    font-family: "Poppins", sans-serif; font-weight: 700;
    font-size: 42px; line-height: 1;
  }
  .person { margin-top: 24px; }
  .person-name {
    font-family: "Poppins", sans-serif; font-weight: 700;
    font-size: 21px; line-height: 1.1;
  }
  .person-role { font-size: 13px; margin-top: 2px; }
  .address { margin-top: 16px; font-size: 13px; line-height: 1.35; }
  .contacts { margin-top: 14px; list-style: none; font-size: 13px; line-height: 1.5; }
  .contacts li { display: flex; align-items: center; gap: 8px; }
  .contacts svg { width: 12px; height: 12px; fill: var(--text-white); flex: none; }
</style>
</head>
<body>
<div class="canvas">
  <section class="card card-back" aria-label="Card reverse">
    <div class="brand-lockup">
      <span class="brand-dot"></span>
      <span class="brand-name-back">Vexalund</span>
    </div>
    <p class="tagline">Care Across Borders</p>
  </section>

  <section class="card card-front" aria-label="Card front">
    <div class="front-content">
      <h1 class="brand-name-front">Vexalund</h1>
      <div class="person">
        <p class="person-name">Ravik S. Tandel</p>
        <p class="person-role">CEO</p>
      </div>
      <p class="address">12, Neelkamal Nagar, Sarvapur<br>441207, India</p>
      <ul class="contacts">
        <li>
          <svg viewBox="0 0 24 24" aria-hidden="true"><path d="M6.6 10.8a15.1 15.1 0 0 0 6.6 6.6l2.2-2.2a1 1 0 0 1 1-.25 11.4 11.4 0 0 0 3.6.57 1 1 0 0 1 1 1V20a1 1 0 0 1-1 1A17 17 0 0 1 3 4a1 1 0 0 1 1-1h3.5a1 1 0 0 1 1 1c0 1.25.2 2.45.57 3.57a1 1 0 0 1-.25 1z"/></svg>
          +919000012345
        </li>
        <li>
          <svg viewBox="0 0 24 24" aria-hidden="true"><path d="M2 5h20v14H2zm2 2v.5l8 5 8-5V7zm0 2.8V17h16V9.8l-8 5z"/></svg>
          rtandel@vexalund.com
        </li>
        <li>
          <svg viewBox="0 0 24 24" aria-hidden="true"><path d="M12 2a10 10 0 1 0 0 20 10 10 0 0 0 0-20zm6.9 9h-3a15 15 0 0 0-1.2-5.6A8 8 0 0 1 18.9 11zM12 4.1c.9 1.3 1.7 3.7 1.9 6.9h-3.8c.2-3.2 1-5.6 1.9-6.9zM9.3 5.4A15 15 0 0 0 8.1 11h-3a8 8 0 0 1 4.2-5.6zM5.1 13h3a15 15 0 0 0 1.2 5.6A8 8 0 0 1 5.1 13zm6.9 6.9c-.9-1.3-1.7-3.7-1.9-6.9h3.8c-.2 3.2-1 5.6-1.9 6.9zm2.7-1.3a15 15 0 0 0 1.2-5.6h3a8 8 0 0 1-4.2 5.6z"/></svg>
          www.vexalund.com
        </li>
      </ul>
    </div>
  </section>
</div>
</body>
</html>
```